Using attached logo that has been created

Business card with logo that's attached. Maybe with water or the cartoon van in background. Looking for it to not be so plain and not too white.
Information to include;
Rodney Ashcombe
(555) 218-7730
Info@bramleypipeworks.example
www.bramleypipeworks.example
License # 4627195
Looking forward to the designs u come up with.
Thank you!
-Delphine
Target Market(s)
Plumbing
Industry/Entity Type
Plumbing
Contact Information for Business Card
Listed above

```html
<!DOCTYPE html>
<html lang="en">
<head>
<meta charset="utf-8">
<title>Bramley Pipeworks – Business Card</title>
<link href="https://fonts.googleapis.com/css2?family=Roboto+Condensed:wght@400;700;800&family=Kalam:wght@400&display=swap" rel="stylesheet">
<style>
  :root {
    --page-bg: #e6e7e9;
    --card-yellow: #fdbe12;
    --card-blue: #1354a8;
    --ink-dark: #1b1b1b;
    --ink-white: #ffffff;
    --figure-top: #2f6cc4;
    --figure-bottom: #8a6a45;
    --van-light: #eceff2;
    --van-dark: #9aa1a8;
  }
  * { box-sizing: border-box; margin: 0; padding: 0; }
  html, body {
    width: 733px;
    height: 1200px;
    overflow: hidden;
    background: var(--page-bg);
  }
  .canvas {
    position: relative;
    width: 733px;
    height: 1200px;
  }
  .business-card {
    position: absolute;
    left: 36px;
    top: 400px;
    width: 660px;
    height: 399px;
    background: var(--card-yellow);
    overflow: hidden;
    box-shadow: 0 3px 10px rgba(0,0,0,0.25);
    font-family: "Roboto Condensed", "Arial Narrow", sans-serif;
  }
  .water-band {
    position: absolute;
    left: 0;
    top: 0;
    width: 660px;
    height: 399px;
  }
  .mascot-illustration {
    position: absolute;
    left: 47px;
    top: 28px;
    width: 115px;
    height: 342px;
    border-radius: 40px 40px 12px 12px;
    background: linear-gradient(180deg, var(--figure-top) 0%, var(--figure-top) 45%, var(--figure-bottom) 60%, var(--figure-bottom) 100%);
  }
  .van-illustration {
    position: absolute;
    left: 196px;
    top: 276px;
    width: 108px;
    height: 60px;
    border-radius: 8px 22px 7px 7px;
    background: linear-gradient(180deg, var(--van-light) 0%, var(--van-light) 70%, var(--van-dark) 100%);
  }
  .brand-name {
    position: absolute;
    right: 61px;
    top: 40px;
    color: var(--card-blue);
    font-weight: 800;
    line-height: 1;
    text-transform: uppercase;
    text-align: right;
  }
  .brand-name .brand-main {
    display: block;
    font-size: 58px;
    letter-spacing: 1px;
  }
  .brand-name .brand-sub {
    display: block;
    font-size: 30px;
    letter-spacing: 3px;
    margin-top: 2px;
  }
  .brand-name .brand-tail {
    display: block;
    font-size: 20px;
    margin-top: 2px;
  }
  .license {
    position: absolute;
    left: 184px;
    top: 138px;
    color: var(--ink-dark);
    font-weight: 700;
    font-size: 17px;
  }
  .person-name {
    position: absolute;
    right: 61px;
    top: 168px;
    color: var(--ink-dark);
    font-family: "Kalam", cursive;
    font-size: 42px;
    line-height: 1.1;
  }
  .contact-list {
    position: absolute;
    right: 61px;
    top: 262px;
    list-style: none;
    text-align: right;
    color: var(--ink-white);
  }
  .contact-list .phone { font-size: 29px; line-height: 36px; }
  .contact-list .email,
  .contact-list .web { font-size: 20px; line-height: 27px; }
</style>
</head>
<body>
<main class="canvas">
  <section class="business-card">
    <svg class="water-band" viewBox="0 0 660 399" aria-hidden="true">
      <path fill="var(--card-blue)" d="M0 262 C15 250 30 246 40 256 C48 264 52 276 60 268 C70 256 90 250 110 258 C128 264 150 246 175 252 C200 258 215 244 240 250 C262 256 270 264 290 252 C310 240 330 254 350 246 C372 238 392 252 412 244 C432 236 448 250 470 240 C492 230 510 246 530 236 C552 226 570 244 590 232 C608 222 622 236 640 226 C648 222 654 214 660 210 L660 399 L0 399 Z"/>
      <path fill="var(--card-blue)" d="M20 256 C16 240 26 236 30 246 C32 252 28 258 20 256 Z"/>
      <path fill="var(--card-blue)" d="M292 250 C290 236 300 234 302 244 C302 250 298 254 292 250 Z"/>
      <path fill="var(--card-blue)" d="M612 230 C608 214 620 210 622 222 C622 228 618 232 612 230 Z"/>
    </svg>

    <div class="mascot-illustration" role="img" aria-label="Cartoon plumber mascot in a blue shirt and khaki trousers holding a pipe wrench and a circular saw"></div>
    <div class="van-illustration" role="img" aria-label="Cartoon white service van driving with speed lines"></div>

    <h1 class="brand-name"><span class="brand-main">Bramley</span><span class="brand-sub">Pipeworks</span><span class="brand-tail">&amp; More</span></h1>
    <p class="license">License #4627195</p>
    <p class="person-name">Rodney Ashcombe</p>

    <ul class="contact-list">
      <li class="phone">(555) 218-7730</li>
      <li class="email">Info@bramleypipeworks.example</li>
      <li class="web">www.bramleypipeworks.example</li>
    </ul>
  </section>
</main>
</body>
</html>
```